kmvalerohub website

I need a new homepage design for my current website at www.KMValeroHub.com. I want someone to look at my current website and develop a more appealing homepage... right now the colors don't blend very well and it needs a facelift

Reason: This has been extended to September 10th

```html
<!DOCTYPE html>
<html lang="en">
<head>
<meta charset="utf-8">
<title>K M Valero — Home</title>
<link href="https://fonts.googleapis.com/css2?family=Lato:ital,wght@0,400;0,700;1,400;1,700&family=Marcellus&family=Raleway:wght@200;800&family=Great+Vibes&display=swap" rel="stylesheet">
<style>
:root{
  --pink:#e9428f;
  --pink-deep:#d93280;
  --pink-soft:#f06aa8;
  --pink-text:#e33d8c;
  --blush:#f3dfe6;
  --ink:#333;
  --muted:#666;
  --navy:#3a4a78;
  --white:#fff;
  --rule:#d8d8d8;
}
*{margin:0;padding:0;box-sizing:border-box}
html,body{width:1150px;height:1200px;overflow:hidden;background:var(--white)}
body{position:relative;font-family:"Lato",sans-serif;color:var(--ink)}
.abs{position:absolute}

.site-header{left:0;top:0;width:1150px;height:73px;background:linear-gradient(var(--pink-soft),var(--pink))}
.brand{left:126px;top:28px;color:var(--white);font-family:"Lato",sans-serif;font-size:24px;font-weight:400;letter-spacing:1px}
.main-nav{left:371px;top:34px;display:flex;gap:40px;list-style:none}
.main-nav li{color:var(--white);font-size:15px}

.hero{left:0;top:73px;width:1150px;height:326px;background:linear-gradient(90deg,#f1dbe2,#f7eef1 50%,#eedde3);overflow:hidden}
.hero-book{left:185px;top:32px;width:184px;height:251px;background:linear-gradient(120deg,#e94590,#f6c9da 60%,#fbe9f0);transform:skewY(-3deg);box-shadow:6px 8px 14px rgba(0,0,0,.2)}
.hero-portrait{left:862px;top:8px;width:200px;height:318px;background:linear-gradient(#6b4a3c,#3d3b40 45%,#2f2d33);border-radius:100px 100px 0 0;z-index:1}
.hero-copy{left:497px;top:62px;width:360px;text-align:center;z-index:2}
.hero-script{font-family:"Great Vibes",cursive;font-size:44px;color:var(--navy);line-height:40px}
.hero-line1{font-family:"Raleway",sans-serif;font-weight:800;font-size:28px;color:var(--pink-text);line-height:30px}
.hero-line2{font-family:"Raleway",sans-serif;font-weight:200;font-size:37px;line-height:40px;letter-spacing:-1.5px;white-space:nowrap}
.hero-line2 .a{color:var(--pink-soft)}.hero-line2 .b{color:var(--navy)}
.hero-line3{font-family:"Marcellus",serif;font-size:28px;color:var(--navy);line-height:34px}
.slider-dots{left:130px;top:302px;display:flex;gap:9px}
.slider-dots span{width:12px;height:12px;border-radius:50%;background:#ccc}
.slider-dots span.on{background:var(--pink)}
.hero-band{left:0;top:399px;width:1150px;height:7px;background:var(--pink)}

.welcome-title{left:130px;top:434px;font-family:"Marcellus",serif;font-weight:400;font-size:25px;color:var(--pink-text)}
.welcome-sub{left:135px;top:471px;font-style:italic;font-size:16px;color:#222}
.welcome-book{left:135px;top:516px;width:88px;height:155px;background:linear-gradient(#e9f5f2,#6cae4a 60%,#3d7a2e);box-shadow:3px 6px 10px rgba(0,0,0,.2)}
.welcome-text{left:249px;top:514px;width:417px;font-style:italic;font-size:11.5px;line-height:17.3px;color:var(--muted);text-align:justify}
.welcome-text p+p{margin-top:17px}
.btn-readmore{left:127px;top:721px;width:109px;height:36px;border-radius:5px;background:var(--pink);color:var(--white);font-weight:700;font-style:italic;font-size:13px;line-height:36px;padding-left:21px}

.report{left:695px;top:422px;width:343px;height:325px;background:var(--pink);border-radius:8px;box-shadow:0 6px 8px rgba(0,0,0,.12)}
.report-top{left:4px;top:4px;width:335px;height:100px}
.report-title{left:0;top:12px;width:343px;text-align:center;font-family:"Marcellus",serif;font-weight:400;font-size:25px;color:var(--pink-text)}
.report-lede{left:14px;top:45px;width:315px;text-align:center;font-size:11.5px;line-height:15px;color:#444}
.field{left:33px;width:291px;height:36px;background:var(--white);border-radius:6px;font-style:italic;font-weight:700;font-size:13px;color:#999;line-height:36px;padding-left:14px}
.btn-subscribe{left:112px;top:210px;width:116px;height:38px;border-radius:7px;background:linear-gradient(#fff,#e6e6e6);color:#222;font-size:15px;text-align:center;line-height:38px;box-shadow:0 1px 2px rgba(0,0,0,.3)}
.report-note{left:22px;top:268px;width:300px;text-align:center;font-size:11.5px;line-height:15px;color:var(--white)}

.divider{left:103px;top:794px;width:939px;height:1px;background:var(--rule)}
.press-arrow{top:837px;width:26px;height:26px;border-radius:50%;background:linear-gradient(#eee,#cfcfcf)}
.press-arrow svg{display:block}
.press-badge{top:830px;height:40px;border-radius:6px}

.site-footer{left:0;top:900px;width:1150px;height:250px;background:var(--pink)}
.foot-title{color:var(--white);font-size:18px;font-weight:400;font-family:"Lato",sans-serif}
.foot-text{color:var(--white);font-size:12px;line-height:23px}
.foot-links{list-style:none;color:var(--white);font-size:11px;line-height:23px}
.social{width:26px;height:26px;border-radius:5px;background:linear-gradient(#9a9a9a,#666)}
.bottom-bar{left:0;top:1150px;width:1150px;height:50px;background:linear-gradient(var(--pink),var(--pink-deep));color:var(--white);font-size:11px}
</style>
</head>
<body>

<header class="site-header abs">
  <div class="brand abs">K M Valero</div>
  <ul class="main-nav abs">
    <li>Home</li><li>About Us</li><li>Products</li><li>Blog</li><li>Forum</li><li>Media Room</li><li>Success Stories</li>
  </ul>
</header>

<section class="hero abs">
  <div class="hero-book abs" role="img" aria-label="Book cover for the weight loss guide"></div>
  <div class="hero-portrait abs" role="img" aria-label="Portrait photo of the author in a dark dress"></div>
  <div class="hero-copy abs">
    <div class="hero-script">Discover</div>
    <div class="hero-line1">SECRETS TO A</div>
    <div class="hero-line2"><span class="a">SLIMMER</span><span class="b">SEXIER</span></div>
    <div class="hero-line3">&amp; HEALTHIER YOU!</div>
  </div>
  <div class="slider-dots abs"><span></span><span></span><span></span><span class="on"></span></div>
</section>
<div class="hero-band abs"></div>

<h1 class="welcome-title abs">WELCOME TO OUR WEBSITE</h1>
<div class="welcome-sub abs">Lose Up to 15 Pounds in 10 Days</div>
<div class="welcome-book abs" role="img" aria-label="Cover of the green smoothie cleanse book"></div>
<div class="welcome-text abs">
  <p>Neque porro quisquam est qui dolorem ipsum quia dolor sit amet, consectetur, adipisci velit. Lorem Ipsum as their default model text, and a search for 'lorem ipsum' will uncover many web sites still in their infancy. Various versions have evolved Duis aute irure dolor in reprehenderit in voluptate velit esse cillum dolore eu fugiat nulla pariatur. Excepteur sint occaecat cupidatat non proident, sunt in culpa qui officia deserunt mollit anim id est laborum</p>
  <p>Neque porro quisquam est, qui dolorem ipsum quia dolor sit amet, consectetur, adipisci velit, sed quia non numquam eius modi tempora incidunt ut labore et dolore magnam aliquam quaerat voluptatem. Ut enim ad minima veniam, quis nostrum exercitationem ullam corporis suscipit laboriosam,</p>
</div>
<div class="btn-readmore abs">Readmore</div>

<aside class="report abs">
  <svg class="report-top abs" viewBox="0 0 335 100" preserveAspectRatio="none" aria-hidden="true">
    <path d="M6 0 H329 Q335 0 335 6 V92 Q168 116 0 92 V6 Q0 0 6 0 Z" fill="#fff"/>
  </svg>
  <h2 class="report-title abs">FREE REPORT</h2>
  <p class="report-lede abs">"5 Reasons You Can't Lose Weight!"<br>Just enter your name and email below to get instant access to this 30 page report absolutely FREE!</p>
  <div class="field abs" style="top:124px">Name</div>
  <div class="field abs" style="top:163px">Email</div>
  <div class="btn-subscribe abs">Subscribe</div>
  <p class="report-note abs">E-mail Privacy: Sign up with complete confidence! We will never sell, rent, lease, or share your information with anyone.</p>
</aside>

<div class="divider abs"></div>
<div class="press-arrow abs" style="left:115px"><svg width="26" height="26"><path d="M15 8 L10 13 L15 18" stroke="#fff" stroke-width="2.5" fill="none"/></svg></div>
<div class="press-badge abs" style="left:158px;width:180px;background:#a0214d"></div>
<div class="press-badge abs" style="left:368px;width:90px;background:#2f7d36"></div>
<div class="press-badge abs" style="left:491px;width:168px;background:#1d8fd3"></div>
<div class="press-badge abs" style="left:688px;width:42px;background:#6d6ab0"></div>
<div class="press-badge abs" style="left:762px;width:44px;border-radius:50%;background:#222"></div>
<div class="press-badge abs" style="left:853px;width:136px;background:var(--pink)"></div>
<div class="press-arrow abs" style="left:1010px"><svg width="26" height="26"><path d="M11 8 L16 13 L11 18" stroke="#fff" stroke-width="2.5" fill="none"/></svg></div>

<footer class="site-footer abs">
  <h3 class="foot-title abs" style="left:116px;top:36px">MY BLOG</h3>
  <p class="foot-text abs" style="left:114px;top:74px;width:280px">Lorem ipsum dolor sit amet, consectetur adipiscing elit. Proin ut purus odio, quis rutrum nibh. Etiam nec tellus malesuada odio tincidunt fringilla quis vitae nisi. Lorem ipsum dolor sit amet, consectetur adipiscing elit. Nullam fringilla malesuada convallis. Morbi laoreet volutpat rhoncus.</p>
  <h3 class="foot-title abs" style="left:440px;top:36px">BROWSE</h3>
  <ul class="foot-links abs" style="left:440px;top:76px"><li>Home</li><li>About Us</li><li>Products</li><li>Blog</li><li>Forum</li><li>Media Room</li></ul>
  <ul class="foot-links abs" style="left:570px;top:76px"><li>Success Stories</li><li>Contact Me</li></ul>
  <div class="social abs" style="left:570px;top:140px"></div>
  <div class="social abs" style="left:604px;top:140px"></div>
  <div class="social abs" style="left:638px;top:140px"></div>
  <h3 class="foot-title abs" style="left:750px;top:36px">WRITE SUCCESS STORIES</h3>
  <p class="foot-text abs" style="left:748px;top:74px;width:290px">Lorem ipsum dolor sit amet, consectetur adipiscing elit. Proin ut purus odio, quis rutrum nibh. Etiam nec tellus malesuada odio tincidunt fringilla quis vitae nisi. Lorem ipsum dolor sit amet, consectetur adipiscing elit. Nullam fringilla malesuada convallis.</p>
  <p class="foot-text abs" style="left:748px;top:202px">Contact Us Now</p>
</footer>

<div class="bottom-bar abs">
  <span class="abs" style="left:115px;top:17px">Copyright © 2014 All Rights Reserved</span>
  <span class="abs" style="left:915px;top:17px">Privacy | Policy</span>
  <span class="abs" style="left:1036px;top:17px">M1</span>
</div>

</body>
</html>
```